ReelBloom business card

We are a performing arts company providing training (to both kids and adults) as well as performers for events. We hope to bring joy and confidence on stage to the people we train, as well as joy to the audience when our artistes perform. Designs should convey the joy, confidence and vibrancy on stage. Design business card using the attached logo. Card to include name, mobile tel, email address, company address, and website. Double sided. To also include the following list of what the company does:
• Training & Enrichment
• Private & Corporate Entertainment
- Music composition & production

Industry/Entity Type

Training

Contact Information for Business Card

Card to include name, mobile tel, email address, company address, and website. Double sided. To also include the following list of what the company does:
• Training & Enrichment

Requirements
Nice to have
• Card need not be the traditional rectangular in shape but not too outrageous.

```html
<!DOCTYPE html>
<html lang="en">
<head>
<meta charset="utf-8">
<title>ReelBloom business card</title>
<link rel="stylesheet" href="https://fonts.googleapis.com/css2?family=Open+Sans:wght@300;400;600&display=swap">
<style>
  :root {
    --page: #e9e7e4;
    --card-white: #ffffff;
    --card-dark: #1c1f26;
    --card-dark-2: #2a2e37;
    --ink: #1f2a5a;
    --name-blue: #2a9fd8;
    --contact: #f1f1f1;
    --svc-yellow: #f2c418;
    --svc-pink: #e2327e;
    --svc-blue: #1e7fd0;
  }
  * { margin: 0; padding: 0; box-sizing: border-box; }
  html, body { width: 1200px; height: 848px; overflow: hidden; }
  body {
    background: var(--page);
    font-family: "Open Sans", Arial, sans-serif;
    display: flex;
    align-items: center;
    justify-content: center;
    gap: 40px;
  }
  .card {
    position: relative;
    width: 540px;
    height: 310px;
    background: var(--card-white);
    border-radius: 12px 42px 12px 42px;
    overflow: hidden;
    box-shadow: 0 10px 28px rgba(0,0,0,0.18);
  }
  .dark-band {
    position: absolute;
    inset: 0;
    background: linear-gradient(160deg, var(--card-dark-2), var(--card-dark) 60%);
  }
  .card-front .dark-band { clip-path: polygon(0 64%, 100% 30%, 100% 100%, 0 100%); }
  .card-back .dark-band { clip-path: polygon(30% 100%, 92% 0, 100% 0, 100% 100%); }
  .music-staff {
    position: absolute;
    border-radius: 4px;
    background: linear-gradient(90deg, rgba(255,255,255,0) 0%, rgba(255,255,255,0.06) 40%, rgba(255,255,255,0.09) 70%, rgba(255,255,255,0) 100%);
  }
  .card-front .music-staff { left: 20px; right: 20px; top: 130px; height: 90px; transform: rotate(-9deg); }
  .card-back .music-staff { left: 330px; right: 0; top: 70px; height: 90px; transform: rotate(-40deg); }
  .brand {
    position: absolute;
    display: flex;
    align-items: center;
    gap: 8px;
    color: var(--ink);
    font-weight: 600;
    font-size: 30px;
    letter-spacing: 0.5px;
    white-space: nowrap;
  }
  .brand-dot { width: 14px; height: 14px; border-radius: 50%; background: var(--ink); }
  .card-front .brand { left: 50%; top: 46px; transform: translateX(-50%); }
  .card-back .brand { left: 40px; top: 60px; }
  .contact {
    position: absolute;
    left: 0; right: 0;
    top: 170px;
    text-align: center;
    color: var(--contact);
  }
  .person-name {
    color: var(--name-blue);
    font-weight: 300;
    font-size: 22px;
    margin-bottom: 8px;
  }
  .contact-line { font-size: 12.5px; font-weight: 400; line-height: 1.45; }
  .services {
    position: absolute;
    right: 22px;
    top: 212px;
    list-style: none;
    font-size: 13px;
    font-weight: 400;
    line-height: 1.5;
    white-space: nowrap;
  }
  .service-training { color: var(--svc-yellow); }
  .service-entertainment { color: var(--svc-pink); }
  .service-music { color: var(--svc-blue); }
</style>
</head>
<body>
  <section class="card card-front">
    <div class="dark-band"></div>
    <div class="music-staff" role="img" aria-label="Music staff lines with floating notes"></div>
    <div class="brand"><span class="brand-dot"></span>ReelBloom</div>
    <div class="contact">
      <p class="person-name">Your Name</p>
      <p class="contact-line">M : 055-41260000</p>
      <p class="contact-line">P : 776-52318800</p>
      <p class="contact-line">E : reelbloom@email.com</p>
      <p class="contact-line">W : www.reelbloom.com</p>
      <p class="contact-line">A : 4512, elm grove road MI 3300 US</p>
    </div>
  </section>

  <section class="card card-back">
    <div class="dark-band"></div>
    <div class="music-staff" role="img" aria-label="Music staff lines with floating notes"></div>
    <div class="brand"><span class="brand-dot"></span>ReelBloom</div>
    <ul class="services">
      <li class="service-training">Training &amp; Enrichment</li>
      <li class="service-entertainment">Private &amp; Corporate Entertainment</li>
      <li class="service-music">Music composition &amp; production</li>
    </ul>
  </section>
</body>
</html>
```